Moravel Aesthetic Doctor

I require an elegant, luxurious looking business card for my aesthetic business. I am a doctor and that will set me aside from competitors. I am planning to provide home and spa based treatments to clients with high expectations. I have attached my logo.

```html
<!DOCTYPE html>
<html lang="en">
<head>
<meta charset="utf-8">
<title>Moravel Aesthetic Doctor – Business Card</title>
<link href="https://fonts.googleapis.com/css2?family=Cinzel:wght@400&family=Roboto:wght@300;400&display=swap" rel="stylesheet">
<style>
  :root {
    --backdrop: #3b3b3d;
    --card: #1b1b1d;
    --sky: #4fb3e8;
    --silver: #a9adb8;
    --silver-light: #c9ccd3;
    --white: #ffffff;
    --mark-ring: #8d9099;
  }
  html, body {
    margin: 0;
    padding: 0;
    width: 799px;
    height: 1200px;
    overflow: hidden;
    background: var(--backdrop);
  }
  .canvas {
    position: relative;
    width: 799px;
    height: 1200px;
  }
  .card {
    position: absolute;
    left: 80px;
    width: 640px;
    height: 366px;
    background: var(--card);
    border-radius: 6px;
    overflow: hidden;
    box-shadow: 0 14px 30px rgba(0,0,0,0.45);
  }
  .card--front { top: 110px; }
  .card--back { top: 700px; }

  /* Front */
  .front-mark {
    position: absolute;
    left: 50%;
    top: 50%;
    transform: translate(-50%, -50%);
    display: flex;
    align-items: center;
    gap: 18px;
  }
  .front-mark__circle {
    width: 46px;
    height: 46px;
    border-radius: 50%;
    border: 3px solid var(--mark-ring);
    box-sizing: border-box;
  }
  .front-mark__name {
    font-family: "Cinzel", serif;
    font-size: 44px;
    letter-spacing: 4px;
    color: var(--mark-ring);
  }

  /* Back */
  .back-waves {
    position: absolute;
    inset: 0;
  }
  .brand {
    position: absolute;
    left: 30px;
    top: 28px;
    display: flex;
    align-items: center;
    gap: 14px;
  }
  .brand__circle {
    width: 52px;
    height: 52px;
    border-radius: 50%;
    border: 3px solid var(--silver);
    box-sizing: border-box;
  }
  .brand__name {
    font-family: "Cinzel", serif;
    font-size: 32px;
    line-height: 1.05;
    letter-spacing: 2px;
    color: var(--silver-light);
  }
  .brand__name span { display: block; font-size: 20px; letter-spacing: 3px; }

  .doctor {
    position: absolute;
    left: 30px;
    top: 120px;
    font-family: "Roboto", sans-serif;
  }
  .doctor__name {
    font-size: 19px;
    font-weight: 300;
    color: var(--silver-light);
  }
  .doctor__name small {
    font-size: 10px;
    margin-left: 6px;
    color: var(--sky);
  }
  .doctor__cred {
    margin-top: 6px;
    font-size: 13px;
    line-height: 1.3;
    color: var(--sky);
  }

  .contact {
    position: absolute;
    right: 26px;
    bottom: 22px;
    font-family: "Roboto", sans-serif;
    font-size: 14px;
    color: var(--white);
    text-align: right;
    line-height: 1.55;
  }
  .contact__row {
    display: flex;
    justify-content: flex-end;
    align-items: center;
    gap: 8px;
  }
  .contact__icon { width: 14px; height: 14px; }
  .contact__dot {
    width: 13px;
    height: 13px;
    border-radius: 50%;
    background: var(--white);
  }
</style>
</head>
<body>
<main class="canvas">

  <section class="card card--front" aria-label="Card front">
    <div class="front-mark">
      <div class="front-mark__circle"></div>
      <div class="front-mark__name">Moravel</div>
    </div>
  </section>

  <section class="card card--back" aria-label="Card back">
    <svg class="back-waves" viewBox="0 0 640 366" preserveAspectRatio="none" aria-hidden="true">
      <path d="M0,180 C140,190 280,260 420,250 C520,243 590,205 640,180" fill="none" stroke="var(--silver)" stroke-width="3"/>
      <path d="M0,198 C150,210 290,285 430,272 C530,262 595,222 640,205 L640,222 C595,240 530,280 430,290 C290,303 150,230 0,218 Z" fill="var(--silver)"/>
      <path d="M0,226 C150,238 290,312 430,300 C530,290 595,250 640,232 L640,366 L0,366 Z" fill="var(--sky)"/>
    </svg>

    <div class="brand">
      <div class="brand__circle"></div>
      <div class="brand__name">Moravel<span>Aesthetic Doctor</span></div>
    </div>

    <div class="doctor">
      <div class="doctor__name">Dr Lena Marsh<small>MRCPCH MD</small></div>
      <div class="doctor__cred">Australasian Diploma of<br>Aesthetic Medicine</div>
    </div>

    <div class="contact">
      <div class="contact__row">Follows: <span class="contact__dot"></span><span class="contact__dot"></span></div>
      <div class="contact__row">0800 555 019
        <svg class="contact__icon" viewBox="0 0 16 16"><path d="M3 1l3 3-2 2c1 2 3 4 5 5l2-2 3 3-2 3C7 15 1 9 1 3z" fill="var(--white)"/></svg>
      </div>
      <div class="contact__row">www.moravel.co.nz
        <svg class="contact__icon" viewBox="0 0 16 16"><rect x="1.5" y="3.5" width="13" height="9" fill="none" stroke="var(--white)" stroke-width="1.4"/><path d="M1.5 3.5L8 9l6.5-5.5" fill="none" stroke="var(--white)" stroke-width="1.4"/></svg>
      </div>
      <div class="contact__row">lena@moravel.co.nz
        <svg class="contact__icon" viewBox="0 0 16 16"><circle cx="8" cy="8" r="6.5" fill="none" stroke="var(--white)" stroke-width="1.3"/><ellipse cx="8" cy="8" rx="3" ry="6.5" fill="none" stroke="var(--white)" stroke-width="1.1"/><path d="M1.5 8h13" stroke="var(--white)" stroke-width="1.1"/></svg>
      </div>
    </div>
  </section>

</main>
</body>
</html>
```